Business Card Design

We need a business card designed for our new company. Prefer a black card with white logo & writing.

Contact Information for Business Card

Ted Galloway, address: 7-4812 Fernhollow Road, Abbotsford, BC, V3K 8R2, Office Phone: 604-712-3390, Cell: 604-947-2164, Email: ted@resinworkshub.ca

Colors

Designer to choose only greyscale colors for use in the design.

```html
<!DOCTYPE html>
<html lang="en">
<head>
<meta charset="utf-8">
<title>Resin Works Hub – Business Card</title>
<link href="https://fonts.googleapis.com/css2?family=Poppins:wght@300;400;700&display=swap" rel="stylesheet">
<style>
  :root {
    --backdrop: #1d1d1f;
    --card: #222225;
    --card-edge: #2e2e32;
    --ink: #f4f4f4;
    --ink-soft: #d8d8d8;
    --emboss: #141416;
    --emboss-light: #2c2c30;
    --rule: #9a9a9a;
  }
  * { box-sizing: border-box; margin: 0; padding: 0; }
  html, body {
    width: 1200px; height: 711px; overflow: hidden;
    background: var(--backdrop);
    font-family: "Poppins", sans-serif;
    color: var(--ink);
  }
  .stage {
    width: 1200px; height: 711px;
    display: flex; align-items: center; justify-content: center; gap: 50px;
  }
  .card {
    position: relative;
    width: 540px; height: 309px;
    background: var(--card);
    border: 1px solid var(--card-edge);
    border-radius: 4px;
  }

  /* Front */
  .card--front { display: flex; align-items: center; justify-content: center; }
  .brand { display: flex; align-items: center; gap: 12px; }
  .brand__dot {
    width: 22px; height: 22px; border-radius: 50%;
    background: var(--ink);
  }
  .brand__name { font-weight: 700; font-size: 30px; letter-spacing: 0.5px; color: var(--ink); }
  .card--front .brand__dot { background: var(--emboss); }
  .card--front .brand__name { color: var(--emboss); }

  /* Back */
  .card--back .brand {
    position: absolute; left: 34px; top: 118px;
  }
  .card--back .brand__name { font-size: 22px; }
  .card--back .brand__dot { width: 16px; height: 16px; }
  .divider {
    position: absolute; left: 268px; top: 52px;
    width: 1px; height: 170px; background: var(--rule);
  }
  .person { position: absolute; left: 296px; top: 54px; }
  .person__name { font-size: 30px; line-height: 1; font-weight: 300; }
  .person__name strong { font-weight: 700; }
  .person__title { font-size: 12px; font-weight: 400; color: var(--ink-soft); margin-top: 4px; }
  .contact { list-style: none; margin-top: 18px; }
  .contact__item {
    display: flex; align-items: center; gap: 10px;
    font-size: 11.5px; font-weight: 300; line-height: 21px;
  }
  .contact__icon { width: 12px; height: 12px; fill: none; stroke: var(--ink); stroke-width: 1.4; }
  .address {
    position: absolute; left: 0; right: 0; bottom: 30px;
    text-align: center; font-size: 13px; font-weight: 300;
  }
</style>
</head>
<body>
<main class="stage">
  <section class="card card--front" aria-label="Card front">
    <div class="brand">
      <span class="brand__dot"></span>
      <span class="brand__name">Resin Works Hub</span>
    </div>
  </section>

  <section class="card card--back" aria-label="Card back">
    <div class="brand">
      <span class="brand__dot"></span>
      <span class="brand__name">Resin Works Hub</span>
    </div>
    <div class="divider"></div>
    <div class="person">
      <h1 class="person__name"><strong>Ted</strong> Galloway</h1>
      <p class="person__title">Founder &amp; CEO</p>
      <ul class="contact">
        <li class="contact__item">
          <svg class="contact__icon" viewBox="0 0 12 12"><path d="M2 1.5l2 .5.6 2.2-1.2 1a6 6 0 0 0 3.4 3.4l1-1.2 2.2.6.5 2c-4.5.8-9.3-4-8.5-8.5z"/></svg>
          604-712-3390
        </li>
        <li class="contact__item">
          <svg class="contact__icon" viewBox="0 0 12 12"><rect x="3" y="1" width="6" height="10" rx="1"/><path d="M5.5 9h1"/></svg>
          604-947-2164
        </li>
        <li class="contact__item">
          <svg class="contact__icon" viewBox="0 0 12 12"><circle cx="6" cy="6" r="5"/><path d="M1 6h10M6 1c2 2 2 8 0 10M6 1c-2 2-2 8 0 10"/></svg>
          www.resinworkshub.ca
        </li>
        <li class="contact__item">
          <svg class="contact__icon" viewBox="0 0 12 12"><rect x="1" y="2.5" width="10" height="7" rx=".5"/><path d="M1 3l5 4 5-4"/></svg>
          ted@resinworkshub.ca
        </li>
      </ul>
    </div>
    <p class="address">7-4812 Fernhollow Road, Abbotsford, BC, V3K 8R2.</p>
  </section>
</main>
</body>
</html>
```